U.S. Popcorn company needs business cards

We are a popcorn company that manufactures popcorn and sells it to grocery stores worldwide. Our theme is "Americana" and our logo is U.S. route 66 which is the most famous highway in the U.S.

We would like the design to be simple and to use both sides. On the back side we would like to see just the logo and website. The front would be normal details

Target Market(s)

Wholesalers, grocers and distributors

Industry/Entity Type

Manufacture

Contact Information for Business Card

Business name: Prairie Lantern Popcorn
Phone: +1 555 308 4726
Email: Dale@prairielanternpopcorn.com
website: www.prairielanternpopcorn.com
Tag Line: "Freshly popped, proudly shared"
Name: Dale Whitcombe
Title: Founder/President

Requirements
Must have
• Either this design should be fun or clean and simple. I will let you show me your thougths.
Nice to have
• Anything that ties in the real Hwy Route 66.
• Colors might need to be red, white and blue incorporated.
Should not have
• Not be too busy.

```html
<!DOCTYPE html>
<html lang="en">
<head>
<meta charset="utf-8">
<title>Prairie Lantern Popcorn – Business Card</title>
<link rel="stylesheet" href="https://fonts.googleapis.com/css2?family=Source+Sans+3:ital,wght@0,400;0,600;0,700;1,600&display=swap">
<style>
  :root {
    --navy: #022463;
    --red: #e3222a;
    --white: #ffffff;
    --ink: #3a3f4a;
    --backdrop: #5b4b3d;
    --card-w: 615px;
    --card-h: 350px;
  }
  * { box-sizing: border-box; margin: 0; padding: 0; }
  html, body {
    width: 1200px;
    height: 987px;
    overflow: hidden;
    background: var(--backdrop);
    font-family: "Source Sans 3", "Segoe UI", sans-serif;
  }
  .card {
    position: absolute;
    left: 293px;
    width: var(--card-w);
    height: var(--card-h);
    overflow: hidden;
  }
  .card--front { top: 130px; background: var(--white); }
  .card--back { top: 505px; background: var(--navy); }

  .front-wave { position: absolute; inset: 0; }

  .brand-name {
    position: absolute;
    display: flex;
    flex-direction: column;
    align-items: center;
    justify-content: center;
    gap: 8px;
    text-align: center;
    font-weight: 700;
    line-height: 1.05;
  }
  .brand-name__dot {
    width: 14px;
    height: 14px;
    border-radius: 50%;
  }
  .card--front .brand-name {
    left: 29px; top: 37px; width: 190px; height: 179px;
    color: var(--navy);
    font-size: 27px;
  }
  .card--front .brand-name__dot { background: var(--red); }

  .holder {
    position: absolute;
    right: 98px;
    top: 140px;
    text-align: right;
  }
  .holder__name {
    color: var(--navy);
    font-size: 22px;
    font-weight: 600;
    line-height: 1.2;
  }
  .holder__title {
    color: var(--red);
    font-size: 16px;
    line-height: 1.3;
  }

  .contacts {
    position: absolute;
    left: 36px;
    top: 252px;
    list-style: none;
    color: var(--ink);
    font-size: 16px;
  }
  .contacts__item {
    display: flex;
    align-items: center;
    gap: 9px;
    height: 23.5px;
  }
  .contacts__icon { width: 15px; height: 15px; flex: none; fill: var(--navy); }

  .card--back .brand-name {
    left: 157px; top: 78px; width: 300px; height: 192px;
    color: var(--white);
    font-size: 34px;
  }
  .card--back .brand-name__dot { background: var(--white); }

  .tagline {
    position: absolute;
    left: 0; right: 0;
    top: 297px;
    text-align: center;
    color: var(--white);
    font-size: 17px;
    font-weight: 600;
    font-style: italic;
  }
</style>
</head>
<body>

<section class="card card--front" aria-label="Business card front">
  <svg class="front-wave" viewBox="0 0 615 350" aria-hidden="true">
    <path d="M515,0 L580,61 C548,95 538,130 541,170 C544,220 583,260 568,300 C553,335 448,325 412,350 L615,350 L615,0 Z" fill="var(--navy)"/>
    <path d="M507,0 L572,61 C540,95 530,130 533,170 C536,220 575,260 560,300 C545,335 440,325 404,350" fill="none" stroke="var(--red)" stroke-width="3.5"/>
  </svg>

  <div class="brand-name">
    <span class="brand-name__dot" aria-hidden="true"></span>
    <span>Prairie Lantern<br>Popcorn</span>
  </div>

  <div class="holder">
    <p class="holder__name">Dale Whitcombe</p>
    <p class="holder__title">Founder/President</p>
  </div>

  <ul class="contacts">
    <li class="contacts__item">
      <svg class="contacts__icon" viewBox="0 0 16 16" aria-hidden="true"><path d="M3.6 1.2l2.3 2.6-1.3 1.8c.9 2 2.4 3.6 4.5 4.6l1.7-1.4 2.6 2.2-1.2 2.4C7.6 13.8 2.4 8.6 1.6 3z"/></svg>
      <span>+1 555 308 4726</span>
    </li>
    <li class="contacts__item">
      <svg class="contacts__icon" viewBox="0 0 16 16" aria-hidden="true"><path d="M1 3.5h14v9H1z M1.8 4.2L8 9l6.2-4.8" stroke="var(--white)" stroke-width="1"/></svg>
      <span>Dale@prairielanternpopcorn.com</span>
    </li>
    <li class="contacts__item">
      <svg class="contacts__icon" viewBox="0 0 16 16" aria-hidden="true"><circle cx="8" cy="8" r="6.8"/><path d="M5 4.5c1.5 0 2 1 1.4 2S4 7.5 4.6 9s1.8 1 2 2.6M10 3.5c-.5 1.2.6 2 1.6 1.8M9.5 9.5c1 0 2 .5 2.4 1.5" fill="none" stroke="var(--white)" stroke-width="1.2"/></svg>
      <span>www.prairielanternpopcorn.com</span>
    </li>
  </ul>
</section>

<section class="card card--back" aria-label="Business card back">
  <div class="brand-name">
    <span class="brand-name__dot" aria-hidden="true"></span>
    <span>Prairie Lantern<br>Popcorn</span>
  </div>
  <p class="tagline">Freshly popped, proudly shared</p>
</section>

</body>
</html>
```